Business Card Design needed - Something Awesome!

Need a business card designed. Company is "Marlowe Advisory" we do consulting and also have sales automation technology.
I'm going to use thick stock or metal, something really nice... I was thinking about a QR Code on the back that would just upload my contact info to the persons contact, etc -

This is a Strategy Company with a tech feel. I'm open to ideas but really want this to be nice!

I need a template that should include:

Name | Position or Title
D: 415.902.3376
www.marloweadvisory.example

I'm going to attach my contact so you can use that one, I need to get this printed.

Target Market(s)

Small to mid size customers, Entrepreneurs etc.

Industry/Entity Type

Consulting, Tech, Private Equity.

Contact Information for Business Card

Name, Phone, Maybe email, URL

Font styles to use
Sans Serif

Colors

Designer to choose only greyscale colors for use in the design.

Requirements
Must have
• Fresh, Clean, stand out from the crowd - will be on thick stock or metal.
Nice to have
• Clean, simple yet impactful.
Should not have
• Not cartoonish

```html
<!DOCTYPE html>
<html lang="en">
<head>
<meta charset="utf-8">
<title>Marlowe Advisory – Business Card</title>
<link rel="stylesheet" href="https://fonts.googleapis.com/css2?family=Arimo:wght@400;700&display=swap">
<style>
  :root {
    --surface: #3b3b3b;
    --card: #141414;
    --silver: #c9c9c9;
    --silver-dim: #a8a8a8;
    --rule: #6a6a6a;
  }
  * { margin: 0; padding: 0; box-sizing: border-box; }
  html, body {
    width: 1200px; height: 801px; overflow: hidden;
    background: var(--surface);
    font-family: "Arimo", Arial, sans-serif;
  }
  .stage {
    width: 1200px; height: 801px;
    display: flex; align-items: center; justify-content: center; gap: 60px;
  }
  .card {
    width: 525px; height: 300px;
    background: var(--card);
    box-shadow: 0 10px 30px rgba(0,0,0,0.45);
    position: relative;
  }
  .card-front {
    display: flex; align-items: center; justify-content: center;
    padding-top: 40px;
  }
  .identity { text-align: right; padding-right: 22px; }
  .identity-name {
    color: var(--silver); font-weight: 700; font-size: 17px; letter-spacing: 0.4px;
    text-transform: uppercase;
  }
  .identity-title { color: var(--silver-dim); font-size: 14px; margin-top: 3px; }
  .divider { width: 1px; height: 62px; background: var(--rule); }
  .contacts { list-style: none; padding-left: 22px; }
  .contacts li {
    display: flex; align-items: center; gap: 8px;
    color: var(--silver); font-size: 14px; line-height: 21px;
  }
  .contacts svg { width: 11px; height: 11px; fill: var(--silver); flex: none; }
  .card-back { display: flex; align-items: center; justify-content: center; }
  .brand { display: flex; align-items: center; gap: 14px; }
  .brand-mark { width: 20px; height: 20px; background: var(--silver); }
  .brand-name {
    color: var(--silver); font-weight: 400; font-size: 60px; letter-spacing: 1px;
  }
</style>
</head>
<body>
<main class="stage">
  <section class="card card-front">
    <div class="identity">
      <p class="identity-name">Adrian K. Sollers</p>
      <p class="identity-title">Founder / CEO</p>
    </div>
    <div class="divider"></div>
    <ul class="contacts">
      <li>
        <svg viewBox="0 0 12 12" aria-hidden="true"><path d="M2.5 1l2 2.2-1 1.3c.7 1.5 1.8 2.6 3.3 3.3l1.3-1 2.2 2-1 1.9C5 10.5 1.5 7 .9 2z"/></svg>
        415.902.3376
      </li>
      <li>
        <svg viewBox="0 0 12 12" aria-hidden="true"><path d="M1 2.5h10v7H1z M1.6 3l4.4 3.4L10.4 3" fill="none" stroke="#c9c9c9" stroke-width="1.1"/></svg>
        info@marloweadvisory.example
      </li>
      <li>
        <svg viewBox="0 0 12 12" aria-hidden="true"><circle cx="6" cy="6" r="5" fill="none" stroke="#c9c9c9" stroke-width="1.1"/><path d="M1 6h10M6 1c-2.2 2.8-2.2 7.2 0 10M6 1c2.2 2.8 2.2 7.2 0 10" fill="none" stroke="#c9c9c9" stroke-width="0.9"/></svg>
        www.marloweadvisory.example
      </li>
    </ul>
  </section>
  <section class="card card-back">
    <div class="brand">
      <span class="brand-mark"></span>
      <span class="brand-name">MARLOWE</span>
    </div>
  </section>
</main>
</body>
</html>
```